Bluefinch Painting needs a Website

We need a website built for a Painting company I own, we mainly do residential painting, but don't want to be limited to that.

Need to have estimate request form.
Need pic's of past projects

I like the look of the website for http://www.harbor-brushworks.com
& "Westlake Home inspections"

My logo that was designed here on ArtHatch on the front page

I would like one of the houses I downloaded as part of the background
of the front page.

Target Market(s)

Home owners

Industry/Entity Type

Painting

Number of Pages Required

1 page

Font styles to use
Serif

Requirements
Must have
• Estimate request form for home owners to fill out -
• Name:
• Phone Number:
• Address:
• E-mail:
• Painting project description:
• And my info to:
• My phone number: (555) 318-7046
• My web address bluefinchpainting.example
Nice to have
• My logo that was designed here on ArtHatch

```html
<!DOCTYPE html>
<html lang="en">
<head>
<meta charset="utf-8">
<title>Bluefinch Painting</title>
<link href="https://fonts.googleapis.com/css2?family=Arimo:wght@400;700&family=Vollkorn:wght@400;500&display=swap" rel="stylesheet">
<style>
:root{
  --blue:#2380c8;
  --blue-dark:#1b6aa8;
  --ink:#1a1a1a;
  --text:#333;
  --footer:#101010;
  --line:#c9c9c9;
  --white:#fff;
}
*{box-sizing:border-box;margin:0;padding:0}
html,body{width:930px;height:1200px;overflow:hidden;background:#fff}
body{position:relative;font-family:"Arimo",Arial,sans-serif;color:var(--text)}
.abs{position:absolute}
.serif{font-family:"Vollkorn",Georgia,serif}

/* header */
.brand{left:123px;top:16px;display:flex;align-items:center;gap:10px}
.brand-mark{width:34px;height:34px;background:var(--blue)}
.brand-name{font-family:"Vollkorn",Georgia,serif;font-size:24px;letter-spacing:1.5px;color:var(--ink);line-height:1}
.trailer{left:503px;top:8px;width:150px;height:70px;background:linear-gradient(#f2f2f2,#cfd3d6);border:1px solid #bbb}
.estimate-btn{left:680px;top:3px;width:116px;height:22px;background:var(--blue);color:#fff;font-size:13px;text-align:center;line-height:22px}
.call{left:683px;top:40px;display:flex;align-items:center;gap:8px}
.call-label{font-size:11px;color:var(--ink)}
.call-number{font-size:16px;color:var(--ink)}

/* nav */
.nav{left:0;top:78px;width:930px;height:31px;background:var(--blue);border-top:1px solid var(--blue-dark)}
.nav ul{list-style:none;position:absolute;left:125px;top:0;display:flex;height:31px}
.nav li{font-family:"Vollkorn",Georgia,serif;font-size:12.5px;color:#fff;height:31px;line-height:31px;padding:0 18px;border-right:1px solid rgba(255,255,255,.35)}
.nav li.active{background:#0d0d0d;font-weight:500;padding:0 11px}
.nav li:last-child{border-right:none}

/* hero */
.hero{left:0;top:109px;width:930px;height:308px;background:linear-gradient(#8fb7df 0%,#b7cde3 22%,#8d8574 45%,#6f6a5a 62%,#3f5a2c 80%,#2f4a24 100%)}
.hero-caption{left:0;top:381px;width:930px;height:36px;background:rgba(35,110,170,.75);color:#fff;font-family:"Vollkorn",Georgia,serif;font-size:18px;text-align:center;line-height:36px}
.hero-arrow{width:28px;height:28px;border-radius:50%;background:rgba(0,0,0,.7);top:217px}

/* welcome */
.welcome{left:0;top:417px;width:930px;height:167px;background:linear-gradient(90deg,#2d2f31,#1d1f21 50%,#2f3133)}
.welcome h1{position:absolute;left:0;width:930px;top:19px;text-align:center;font-family:"Vollkorn",Georgia,serif;font-weight:400;font-size:17px;color:#fff}
.welcome p{position:absolute;left:138px;width:654px;top:65px;text-align:center;font-size:9.5px;line-height:17px;color:#fff}
.welcome-btn{left:435px;top:129px;width:60px;height:18px;background:#000;color:#fff;font-size:9.5px;text-align:center;line-height:18px}

/* content */
.col-title{font-family:"Vollkorn",Georgia,serif;font-size:17.5px;color:var(--ink);top:601px}
.service-img{top:633px;width:206px;height:130px;border:3px solid #e3e3e3}
.service-text{top:770px;width:210px;font-size:9.5px;line-height:14.5px}
.btn-dark{height:18px;background:#000;color:#fff;font-size:9.5px;line-height:18px;text-align:center}
.form-rule{left:607px;top:626px;width:203px;border-top:1px dashed #aaa}
.field{left:609px;width:198px;height:20px;border:1px solid #ccc;border-radius:2px;font-size:8.5px;font-style:italic;color:#666;padding:4px 8px;background:#fff}
.submit{left:614px;top:819px;width:60px;height:18px;background:#000;color:#fff;font-size:10px;font-weight:700;line-height:18px;text-align:center}
.divider{left:133px;top:865px;width:670px;height:3px;background:radial-gradient(ellipse at center,#ddd 0%,rgba(255,255,255,0) 70%)}

/* gallery */
.gallery-icon{left:137px;top:885px;width:40px;height:40px;border-radius:50%;border:1px solid #ccc}
.gallery-title{left:186px;top:893px;font-family:"Vollkorn",Georgia,serif;font-size:17.5px;color:var(--ink)}
.g-arrow{top:898px;width:14px;height:14px}
.thumb{top:932px;width:120px;height:96px;border:1px solid #333;padding:3px;background:#fff}
.thumb div{width:100%;height:100%}

/* footer */
.footer{left:0;top:1042px;width:930px;height:132px;background:var(--footer);color:#fff}
.f-head{font-size:10px;font-weight:700;padding-bottom:3px;border-bottom:1px dashed #666}
.f-list{list-style:none;font-size:9.5px;line-height:15.5px}
.f-row{display:flex;font-size:9.5px;line-height:13.5px}
.f-row b{width:22px;font-weight:700}
.f-time{display:flex;align-items:center;gap:7px;font-size:9px}
.f-brand{left:658px;top:1070px;display:flex;align-items:center;gap:7px}
.f-brand .brand-mark{width:18px;height:18px;background:#ddd}
.f-brand span{font-family:"Vollkorn",Georgia,serif;font-size:15px;letter-spacing:1px;color:#ddd}
.accept{left:658px;top:1104px;width:146px;text-align:center;font-size:9.5px}
.card{top:1121px;width:22px;height:14px;border-radius:2px;background:#9a9a9a}
.copyright{left:0;top:1174px;width:930px;height:26px;background:var(--blue);color:#fff;font-size:9px;text-align:center;line-height:26px}
</style>
</head>
<body>

<header>
  <div class="abs brand"><div class="brand-mark"></div><span class="brand-name">BLUEFINCH PAINTING</span></div>
  <div class="abs trailer" role="img" aria-label="Company work trailer with painting services lettering"></div>
  <div class="abs estimate-btn">Free Estimates</div>
  <div class="abs call">
    <svg width="22" height="22" viewBox="0 0 22 22"><circle cx="11" cy="11" r="10" fill="none" stroke="#2380c8" stroke-width="1.5"/><path d="M8 6c-1 1-1 3 0 5s3 4 5 5c1 .3 2 0 2.5-.8l-1.8-1.6-1.2.8c-1.2-.6-2.3-1.8-2.8-3l.8-1.2L9 6.5z" fill="#2380c8"/></svg>
    <div><div class="call-label">Call Us Today</div><div class="call-number">555-318-7046</div></div>
  </div>
</header>

<nav class="abs nav">
  <ul>
    <li class="active">Home</li><li>About Us</li><li>Exterior</li><li>Interior</li><li>Residential</li><li>Commerical</li><li>Past Projects</li><li>Contact Us</li>
  </ul>
</nav>

<section>
  <div class="abs hero" role="img" aria-label="Two-storey beige house with grey roof, garage and flowering garden"></div>
  <div class="abs hero-arrow" style="left:88px"><svg width="28" height="28"><path d="M16 8l-6 6 6 6" fill="none" stroke="#fff" stroke-width="1.5"/></svg></div>
  <div class="abs hero-arrow" style="left:814px"><svg width="28" height="28"><path d="M12 8l6 6-6 6" fill="none" stroke="#fff" stroke-width="1.5"/></svg></div>
  <div class="abs hero-caption">PROVIDING QUALITY WORK AT AFFORDABLE PRICES</div>
</section>

<section class="abs welcome" role="img" aria-label="Dimmed photo of company work trucks and trailers">
  <h1>Welcome to Bluefinch Painting</h1>
  <svg class="abs" style="left:339px;top:43px" width="268" height="10"><line x1="0" y1="2" x2="268" y2="2" stroke="#fff"/><line x1="0" y1="6" x2="268" y2="6" stroke="#fff"/><path d="M130 0l8 8M138 0l-8 8" stroke="#fff"/></svg>
  <p>Lorem ipsum dolor sit amet, consectetuer adipiscing elit, sed diam nonummy nibh euismod &nbsp;rent ut laoreet dolore magna aliquam erat volutpat. Ut wisi enim ad minim veniam, quis nostrud lore xererci tation ullamcorper suscipit lobortis nisl ut aliquip ex ea commodo consequat. Duis autem revel eum iriure dolor in hendrerit in vulputate velit esse molestie consequat.</p>
  <svg class="abs" style="left:369px;top:132px" width="192" height="12"><line x1="0" y1="6" x2="54" y2="6" stroke="#fff"/><line x1="138" y1="6" x2="192" y2="6" stroke="#fff"/><path d="M54 2h10M54 6h10M54 10h10M128 2h10M128 6h10M128 10h10" stroke="#fff"/></svg>
  <div class="abs welcome-btn" style="left:435px">Read More</div>
</section>

<main>
  <h2 class="abs col-title" style="left:133px">Residential Painting</h2>
  <div class="abs service-img" style="left:133px;background:linear-gradient(120deg,#7b6a58,#c9a57a 50%,#e8e4de)" role="img" aria-label="Furnished living room with freshly painted walls"></div>
  <p class="abs service-text" style="left:134px">Sed ut perspiciatis unde omnis iste natus error sit voluptatem accusantium doloremque laudantium, totam rem aperiam.</p>
  <div class="abs btn-dark" style="left:133px;top:819px;width:61px">Read More</div>

  <h2 class="abs col-title" style="left:370px">Commerical Painting</h2>
  <div class="abs service-img" style="left:370px;background:linear-gradient(90deg,#d8d6cd,#efeee8 60%,#1a2a44)" role="img" aria-label="Painter on a ladder rolling paint onto a white wall"></div>
  <p class="abs service-text" style="left:373px">Sed ut perspiciatis unde omnis iste natus error sit voluptatem accusantium doloremque laudantium, totam rem aperiam.</p>
  <div class="abs btn-dark" style="left:373px;top:819px;width:61px">Read More</div>

  <h2 class="abs col-title" style="left:607px">Quick Inquiry</h2>
  <div class="abs form-rule"></div>
  <form>
    <div class="abs field" style="top:637px">Name</div>
    <div class="abs field" style="top:665px">Email</div>
    <div class="abs field" style="top:694px">Phone</div>
    <div class="abs field" style="top:722px">Type of Work</div>
    <div class="abs field" style="top:753px;height:58px">Message</div>
    <div class="abs submit">Submit</div>
  </form>
  <div class="abs divider"></div>

  <div class="abs gallery-icon"><svg width="40" height="40"><rect x="13" y="12" width="14" height="14" fill="none" stroke="#333" stroke-width="2"/><rect x="16" y="15" width="8" height="8" fill="#333"/><path d="M10 15v14h14" fill="none" stroke="#333" stroke-width="2"/></svg></div>
  <h2 class="abs gallery-title">Our Work Gallery</h2>
  <svg class="abs g-arrow" style="left:770px" viewBox="0 0 14 14"><rect width="14" height="14" fill="#111"/><path d="M9 3l-4 4 4 4" fill="none" stroke="#fff" stroke-width="2"/></svg>
  <svg class="abs g-arrow" style="left:786px" viewBox="0 0 14 14"><rect width="14" height="14" fill="#2380c8"/><path d="M5 3l4 4-4 4" fill="none" stroke="#fff" stroke-width="2"/></svg>

  <div class="abs thumb" style="left:137px"><div style="background:linear-gradient(#e7d6b8,#a0623a)" role="img" aria-label="Entry hall with staircase and wood floor"></div></div>
  <div class="abs thumb" style="left:271px"><div style="background:linear-gradient(#2e6fb6,#c7cdd6 40%,#8d96a3)" role="img" aria-label="Painter working on a house gable"></div></div>
  <div class="abs thumb" style="left:405px"><div style="background:linear-gradient(90deg,#c99a3a,#e6c25a 50%,#d9cfae)" role="img" aria-label="Yellow painted hallway"></div></div>
  <div class="abs thumb" style="left:539px"><div style="background:linear-gradient(#a9c8e8,#b9a891 50%,#4d8a3a)" role="img" aria-label="Two-storey house with lawn and palms"></div></div>
  <div class="abs thumb" style="left:672px"><div style="background:linear-gradient(90deg,#c8a46a,#f3eee2 60%,#d8c29a)" role="img" aria-label="Bright staircase with potted plant"></div></div>
</main>

<footer class="abs footer">
  <div class="abs" style="left:133px;top:15px">
    <div class="f-head" style="width:74px">Quick Links</div>
    <ul class="f-list" style="margin-top:6px"><li>• Home</li><li>• About Us</li><li>• Services</li><li>• Past Projects</li><li>• Contact Us</li></ul>
  </div>
  <div class="abs" style="left:290px;top:15px">
    <div class="f-head" style="width:116px">Contact Information</div>
    <div class="f-row" style="margin-top:7px"><b>A:</b><span>Bluefinch Painting<br>Street Name City Name<br>State Zipcode</span></div>
    <div class="f-row" style="margin-top:6px"><b>P:</b><span>555-318-7046</span></div>
    <div class="f-row" style="margin-top:5px"><b>E:</b><span>inquiry@bluefinchp.example</span></div>
  </div>
  <div class="abs" style="left:472px;top:15px">
    <div class="f-head" style="width:111px">Work Times</div>
    <div class="f-time" style="margin-top:9px"><svg width="11" height="11"><rect x="1" y="3" width="9" height="7" fill="#fff"/><rect x="3" y="1" width="5" height="2" fill="#fff"/></svg>Our work timings are:</div>
    <div class="f-time" style="margin-top:10px"><svg width="11" height="11"><circle cx="5.5" cy="5.5" r="4.5" fill="none" stroke="#fff"/><path d="M5.5 3v3h2" fill="none" stroke="#fff"/></svg>Monday - Friday. 8AM - 8PM</div>
    <div class="f-time" style="margin-top:10px"><svg width="11" height="11"><circle cx="5.5" cy="5.5" r="4.5" fill="none" stroke="#fff"/><path d="M5.5 3v3h2" fill="none" stroke="#fff"/></svg>Saturday:9AM - 4PM</div>
    <div class="f-time" style="margin-top:10px"><svg width="11" height="11"><circle cx="5.5" cy="5.5" r="4.5" fill="none" stroke="#fff"/><path d="M3.5 7.5h4" stroke="#fff"/></svg>Sunday: closed</div>
  </div>
</footer>
<div class="abs f-brand"><div class="brand-mark"></div><span>BLUEFINCH PAINTING</span></div>
<div class="abs accept" style="color:#fff">We Accept</div>
<div class="abs card" style="left:673px"></div>
<div class="abs card" style="left:697px"></div>
<div class="abs card" style="left:721px"></div>
<div class="abs card" style="left:745px"></div>
<div class="abs card" style="left:769px"></div>
<div class="abs copyright">Copyright ©2015, BluefinchPainting &nbsp;All Rights Reserved</div>

</body>
</html>
```